Homemaking training schools needs a Business Card design

Designer, Hello!

No special requirements, good-looking enough.
--------------------------------------------------------------------------

Name: Marcus Dole
Chairman
Tel: 0574-71948263
Mobile: 13857420916
Email: kelvora@mailnest.example
Web: www.prt2019.example
Add: No.258, LanpingJie, BeiyuanQu, Ningbo, Zhejiang

LOGO
Ningbo PRT Homemaking Training School

Target Market(s)

pregnant women, mothers, infants, the elderly and families, including cleaning, cooking, nursing training.

Industry/Entity Type

Business

Contact Information for Business Card

Name: Marcus Dole
Chairman
Tel: 0574-71948263
Mobile: 13857420916
Email: kelvora@mailnest.example
Web: www.prt2019.example

LOGO

Font styles to use
Serif
Sans Serif
Decorative

Requirements
Nice to have
• Feels: clean, specifications, safety, comfort, warmth and happiness.

```html
<!DOCTYPE html>
<html lang="en">
<head>
<meta charset="utf-8">
<title>PuRenTang Business Card</title>
<link href="https://fonts.googleapis.com/css2?family=Montserrat:wght@400;500;600;700;800&display=swap" rel="stylesheet">
<style>
  :root {
    --backdrop: #2b2b2d;
    --card: #000000;
    --pink: #ec0f8c;
    --blue: #0f78c4;
    --white: #ffffff;
  }
  * { box-sizing: border-box; margin: 0; padding: 0; }
  html, body { width: 1200px; height: 900px; overflow: hidden; }
  body {
    background: var(--backdrop);
    font-family: "Montserrat", Arial, sans-serif;
    color: var(--white);
    position: relative;
  }
  .card {
    position: absolute;
    left: 285px;
    width: 630px;
    height: 360px;
    background: var(--card);
    border-radius: 22px;
    overflow: hidden;
  }
  .card--front { top: 60px; }
  .card--back { top: 480px; }

  .brand-dot {
    border-radius: 50%;
    background: var(--pink);
    flex: none;
  }
  .brand-name {
    font-weight: 700;
    color: var(--blue);
    letter-spacing: -0.5px;
    white-space: nowrap;
  }

  /* Front */
  .front-row {
    position: absolute;
    left: 64px; right: 40px; top: 126px;
    display: flex; align-items: center; gap: 40px;
  }
  .front-brand { display: flex; align-items: center; gap: 14px; }
  .front-brand .brand-dot { width: 44px; height: 44px; }
  .front-brand .brand-name { font-size: 34px; }
  .front-web {
    font-weight: 600; font-size: 18px; white-space: nowrap;
  }
  .front-web .accent { color: var(--pink); }
  .front-stripe {
    position: absolute; left: 0; right: 0; bottom: 0; height: 44px;
    display: flex;
  }
  .front-stripe span:nth-child(1) { flex: 0 0 240px; background: var(--white); }
  .front-stripe span:nth-child(2) { flex: 0 0 230px; background: var(--pink); }
  .front-stripe span:nth-child(3) { flex: 1; background: var(--white); }

  /* Back */
  .holder {
    position: absolute; right: 34px; top: 30px; text-align: right;
  }
  .holder-name {
    font-weight: 800; font-size: 26px; color: var(--blue); letter-spacing: 0.5px;
  }
  .holder-title {
    font-weight: 600; font-size: 12px; color: var(--pink); letter-spacing: 1px;
  }
  .name-rule {
    position: absolute; left: 0; top: 72px; width: 470px; height: 1.5px;
    background: var(--blue);
  }
  .address {
    position: absolute; right: 34px; top: 108px; text-align: right;
    font-weight: 600; font-size: 13px; line-height: 1.45;
  }
  .contacts {
    position: absolute; right: 34px; top: 172px; list-style: none;
    font-weight: 600; font-size: 14px; line-height: 1.5;
  }
  .contacts li { display: flex; justify-content: flex-end; align-items: center; gap: 8px; }
  .contacts svg { width: 11px; height: 11px; flex: none; }
  .back-brand {
    position: absolute; left: 40px; bottom: 70px;
    display: flex; align-items: center; gap: 12px;
  }
  .back-brand .brand-dot { width: 28px; height: 28px; }
  .back-brand .brand-name { font-size: 42px; }
  .brand-rule {
    position: absolute; left: 40px; bottom: 60px; width: 290px; height: 1.5px;
    background: var(--white);
  }
  .back-stripe {
    position: absolute; left: 0; right: 0; bottom: 0; height: 40px; display: flex;
  }
  .back-stripe span:nth-child(1) { flex: 0 0 230px; background: var(--blue); }
  .back-stripe span:nth-child(2) { flex: 0 0 230px; background: var(--pink); }
  .back-stripe span:nth-child(3) { flex: 1; background: var(--blue); }
</style>
</head>
<body>

<section class="card card--front">
  <div class="front-row">
    <div class="front-brand">
      <span class="brand-dot"></span>
      <span class="brand-name">PuRenTang</span>
    </div>
    <p class="front-web">www.<span class="accent">prt2019</span>.example</p>
  </div>
  <div class="front-stripe"><span></span><span></span><span></span></div>
</section>

<section class="card card--back">
  <div class="holder">
    <p class="holder-name">MARCUS DOLE</p>
    <p class="holder-title">CHAIRMAN</p>
  </div>
  <div class="name-rule"></div>

  <p class="address">No.258, LanpingJie<br>BeiyuanQu, Ningbo, Zhejiang</p>

  <ul class="contacts">
    <li>0574-71948263
      <svg viewBox="0 0 12 12"><path d="M2 1l2 0 1 3-1.5 1a6 6 0 0 0 3.5 3.5L8 7l3 1v2a1 1 0 0 1-1 1A9 9 0 0 1 1 2a1 1 0 0 1 1-1z" fill="var(--pink)"/></svg>
    </li>
    <li>13857420916
      <svg viewBox="0 0 12 12"><rect x="3" y="0.5" width="6" height="11" rx="1" fill="none" stroke="var(--pink)" stroke-width="1.3"/><circle cx="6" cy="9.5" r="0.7" fill="var(--pink)"/></svg>
    </li>
    <li>kelvora@mailnest.example
      <svg viewBox="0 0 12 12"><rect x="0.7" y="2" width="10.6" height="8" rx="1" fill="none" stroke="var(--pink)" stroke-width="1.3"/><path d="M1 2.5l5 4 5-4" fill="none" stroke="var(--pink)" stroke-width="1.3"/></svg>
    </li>
    <li>www.prt2019.example
      <svg viewBox="0 0 12 12"><circle cx="6" cy="6" r="5.2" fill="none" stroke="var(--pink)" stroke-width="1.3"/><path d="M1 6h10M6 1c-2.5 3-2.5 7 0 10M6 1c2.5 3 2.5 7 0 10" fill="none" stroke="var(--pink)" stroke-width="1"/></svg>
    </li>
  </ul>

  <div class="back-brand">
    <span class="brand-dot"></span>
    <span class="brand-name">PuRenTang</span>
  </div>
  <div class="brand-rule"></div>

  <div class="back-stripe"><span></span><span></span><span></span></div>
</section>

</body>
</html>
```